A clean crisp business card for a Landscape Construction company. Designed to be easy to read contact/ info and also be appealing/interesting, unlike a traditional business card.

Industry/Entity Type

Landscape Construction

Contact Information for Business Card

Company name : Brambleford Landscape Construction, phone number: (877) 62Vista, website:Bramblefordyards.example, Email, sales@bramblefordyards.example

Requirements
Nice to have
• Luxurious finishes/ details…. Icons or emblems next to contact info
Should not have
• Clipart or general pictures

```html
<!DOCTYPE html>
<html lang="en">
<head>
<meta charset="utf-8">
<title>Brambleford Landscape Construction – Business Card</title>
<link rel="stylesheet" href="https://fonts.googleapis.com/css2?family=Montserrat:wght@400;500;700&display=swap">
<style>
  :root {
    --page: #e8e8e6;
    --card: #2b2b29;
    --blue: #1f6cbf;
    --green: #8cc63f;
    --white: #f2f2f2;
    --faint: rgba(140, 198, 63, 0.12);
  }
  * { box-sizing: border-box; margin: 0; padding: 0; }
  html, body {
    width: 1200px; height: 1143px; overflow: hidden;
    background: var(--page);
    font-family: "Montserrat", Arial, sans-serif;
  }
  .card {
    position: absolute; left: 170px;
    width: 860px; height: 491px;
    background: var(--card);
    border-radius: 4px;
    box-shadow: 0 14px 30px rgba(0,0,0,0.18);
    overflow: hidden;
  }
  .card--front { top: 60px; }
  .card--back { top: 596px; }

  .brand {
    color: var(--green);
    font-weight: 700;
    text-transform: uppercase;
    line-height: 1.15;
  }
  .card--front .brand {
    position: absolute; left: 0; right: 0; top: 150px;
    text-align: center; font-size: 52px; letter-spacing: 3px;
  }
  .card--front .brand small {
    display: block; font-size: 22px; letter-spacing: 8px; margin-top: 8px;
  }
  .card--front .website {
    position: absolute; left: 0; right: 0; top: 330px;
    text-align: center; color: var(--blue);
    font-size: 22px; font-weight: 500; letter-spacing: 0.5px;
  }

  .card--back .brand {
    position: absolute; left: 70px; top: 60px;
    font-size: 34px; letter-spacing: 2px;
  }
  .card--back .brand small {
    display: block; font-size: 14px; letter-spacing: 5px; margin-top: 6px;
  }
  .contact-list {
    position: absolute; left: 70px; top: 245px;
    list-style: none;
  }
  .contact-list li {
    display: flex; align-items: center; gap: 18px;
    color: var(--white); font-size: 21px; margin-bottom: 18px;
  }
  .contact-icon {
    width: 26px; height: 26px; flex: none;
  }
  .person {
    position: absolute; left: 560px; top: 250px;
  }
  .person-name {
    color: var(--blue); font-weight: 700; font-size: 27px; letter-spacing: 0.5px;
  }
  .person-role {
    color: var(--white); font-size: 22px; margin-top: 6px;
  }
  .decor-circle {
    position: absolute; left: 600px; top: 360px;
    width: 230px; height: 230px; border-radius: 50%;
    background: var(--faint);
  }
</style>
</head>
<body>

<section class="card card--front">
  <h1 class="brand">Brambleford<small>Landscape Construction</small></h1>
  <p class="website">www.bramblefordyards.example</p>
</section>

<section class="card card--back">
  <h2 class="brand">Brambleford<small>Landscape Construction</small></h2>

  <ul class="contact-list">
    <li>
      <svg class="contact-icon" viewBox="0 0 26 26" aria-hidden="true">
        <circle cx="13" cy="13" r="13" fill="#1f6cbf"/>
        <path d="M9 7.5c.6-.4 1.3-.3 1.6.3l1 2c.2.5.1 1-.3 1.3l-.8.6c.6 1.5 1.6 2.6 3 3.3l.7-.8c.4-.4.9-.5 1.3-.3l2 1c.6.3.7 1 .3 1.6l-.8 1.1c-.5.6-1.3.8-2 .5-3.4-1.4-5.7-3.9-6.7-7.2-.2-.7 0-1.4.6-1.9z" fill="#f2f2f2"/>
      </svg>
      (877) 62Vista
    </li>
    <li>
      <svg class="contact-icon" viewBox="0 0 26 26" aria-hidden="true">
        <circle cx="13" cy="13" r="13" fill="#1f6cbf"/>
        <rect x="7" y="9" width="12" height="8.5" rx="1" fill="#f2f2f2"/>
        <path d="M7.3 9.4 13 14l5.7-4.6" fill="none" stroke="#1f6cbf" stroke-width="1.2"/>
      </svg>
      sales@bramblefordyards.example
    </li>
    <li>
      <svg class="contact-icon" viewBox="0 0 26 26" aria-hidden="true">
        <circle cx="13" cy="13" r="13" fill="#8cc63f"/>
        <g fill="none" stroke="#f2f2f2" stroke-width="1.2">
          <circle cx="13" cy="13" r="6.5"/>
          <ellipse cx="13" cy="13" rx="2.8" ry="6.5"/>
          <path d="M6.5 13h13M7.5 9.8h11M7.5 16.2h11"/>
        </g>
      </svg>
      www.bramblefordyards.example
    </li>
  </ul>

  <div class="person">
    <p class="person-name">Marcus Hale</p>
    <p class="person-role">Managing Director</p>
  </div>

  <div class="decor-circle" aria-hidden="true"></div>
</section>

</body>
</html>
```